Marlowby Services Website Design

We have most content but require a professional design. We have a logo already and will need it utilized along with several of the photos from the attached documentation.
First page should have our mission and Vision and the synapsis provided in the word document. Visitors will be prompted to select from one of our 3 divisions from this page.
Each division will have the same list of tabs : About, Services, Safety, Careers and Contact.
Photos on each divisions page should be representative of the divisions offerings. The word doc attached contains the requested content and we are open to edits that would complement and fill the website.
I like the Quorvane site www.quorvane.example - they are our competition so cant be modeled directly after this.
Please include prompts to request quote at each service page. align the format of the geotechnical page to the other 2 divisions.
I used chat gpt for some of the content so will need it optimized for SCO.

```html
<!DOCTYPE html>
<html lang="en">
<head>
<meta charset="utf-8">
<title>Marlowby Services</title>
<link href="https://fonts.googleapis.com/css2?family=Lato:wght@400;700&family=Montserrat:wght@500&family=Orbitron:wght@500;700;800&family=Oswald:wght@500&display=swap" rel="stylesheet">
<style>
:root{
  --red:#e8202a;
  --ink:#1c1c1c;
  --grey:#f3f3f3;
  --muted:#4a4a4a;
  --dark:#151515;
  --white:#ffffff;
}
*{margin:0;padding:0;box-sizing:border-box}
html,body{width:1200px;height:3367px;overflow:hidden}
body{position:relative;background:var(--white);font-family:'Lato',sans-serif;color:var(--ink)}
.abs{position:absolute}
.brand{font-family:'Orbitron',sans-serif;font-weight:800;color:var(--red);letter-spacing:2px}
.btn{position:absolute;background:var(--red);color:var(--white);font-family:'Lato',sans-serif;font-size:15px;display:flex;align-items:center;justify-content:center;text-decoration:none}
.site-header{position:absolute;left:0;top:0;width:1200px;height:60px;background:var(--white)}
.site-header .brand{position:absolute;left:144px;top:8px;font-size:38px}
.main-nav a{position:absolute;top:21px;font-size:13px;color:var(--ink);text-decoration:none}
.hero{position:absolute;left:0;top:60px;width:1200px;height:550px;background:linear-gradient(180deg,#1d3f7a 0%,#6b6a8c 25%,#e47a3a 50%,#d4381d 64%,#2a3e78 72%,#152650 100%)}
.hero-title{position:absolute;left:144px;top:230px;font-family:'Oswald',sans-serif;font-weight:500;font-size:38px;line-height:44px;color:var(--white)}
.hero-sub{position:absolute;left:144px;top:327px;font-family:'Montserrat',sans-serif;font-weight:500;font-size:23px;line-height:30px;color:var(--white)}
.section-title{position:absolute;left:0;width:1200px;text-align:center;font-family:'Orbitron',sans-serif;font-weight:800;font-size:34px;color:var(--red);letter-spacing:1px}
.section-lead{position:absolute;left:0;width:1200px;text-align:center;font-size:15px;top:730px}
.service-card{position:absolute;width:297px;height:298px;background:var(--grey);text-align:center}
.service-card .icon{width:78px;height:78px;margin:0 auto;background:#f6d4d6;border-radius:8px}
.service-card h3{font-family:'Orbitron',sans-serif;font-weight:500;font-size:15.5px;line-height:18px;color:var(--ink);margin-top:16px}
.service-card p{font-size:12.5px;line-height:20.5px;color:#333;width:240px;margin:16px auto 0}
.about-photo{position:absolute;left:0;top:1490px;width:554px;height:573px;background:linear-gradient(180deg,#4c5a48 0%,#8a9384 35%,#c9cbc7 55%,#8d8a84 80%,#7a7771 100%)}
.about-panel{position:absolute;left:427px;top:1583px;width:773px;height:546px;background:var(--grey)}
.about-heading{position:absolute;left:652px;font-family:'Orbitron',sans-serif;font-weight:500;font-size:26px;color:var(--ink)}
.about-text{position:absolute;left:598px;width:460px;font-size:12px;line-height:21.6px;color:var(--muted)}
.division{position:absolute;top:2306px;width:282px;height:313px;color:var(--white)}
.division h3{position:absolute;left:16px;font-family:'Orbitron',sans-serif;font-weight:500;font-size:14.5px;line-height:16px;letter-spacing:.5px}
.division p{position:absolute;left:19px;top:212px;width:240px;font-size:11px;line-height:20px}
.division .go{position:absolute;right:14px;bottom:20px;width:20px;height:20px}
.tagline{position:absolute;left:0;top:2737px;width:1200px;text-align:center;font-weight:700;font-size:25.5px;line-height:32px}
.tagline .brand-word{font-family:'Orbitron',sans-serif;font-weight:700;color:var(--red)}
.site-footer{position:absolute;left:0;top:2951px;width:1200px;height:416px;background:var(--dark);color:var(--white)}
.site-footer .rule{position:absolute;left:141px;width:919px;height:1px;background:#3a3a3a}
.footer-nav a{position:absolute;top:197px;font-size:13px;color:var(--white);text-decoration:none}
.contact-item{position:absolute;top:295px;display:flex;gap:10px;font-size:12.5px;line-height:20px}
.contact-item strong{font-family:'Orbitron',sans-serif;font-weight:500;font-size:13px}
.copyright{position:absolute;left:0;top:379px;width:1200px;text-align:center;font-size:11.5px}
</style>
</head>
<body>

<header class="site-header">
  <div class="brand">MARLOWBY</div>
  <nav class="main-nav">
    <a style="left:644px" href="#">About</a>
    <a style="left:716px" href="#">Services</a>
    <a style="left:801px" href="#">Safety</a>
    <a style="left:874px" href="#">Careers</a>
  </nav>
  <a class="btn" href="#" style="left:942px;top:13px;width:118px;height:33px">Contact Us</a>
</header>

<section class="hero" role="img" aria-label="Oil pump jacks silhouetted against a sunset above a field of solar panels">
  <h1 class="hero-title" style="top:170px">Delivering Safe, Reliable Aerial<br>Access &amp; Maintenance Service</h1>
  <p class="hero-sub" style="top:267px">To Oil &amp; Gas,Construction, Utility,<br>&amp; Renewable energy Sector</p>
  <a class="btn" href="#" style="left:141px;top:342px;width:116px;height:34px">Contact Us</a>
</section>

<h2 class="section-title" style="top:675px">OUR SERVICES</h2>
<p class="section-lead">Delivering safe, reliable aerial access and maintenance services</p>

<article class="service-card" style="left:453px;top:771px;padding-top:40px">
  <div class="icon" role="img" aria-label="Refinery line icon"></div>
  <h3 style="margin-top:22px">Oil&amp;Gas</h3>
  <p style="margin-top:18px">Lorem ipsum dolor sit amet, consectetur adipiscing elit, sed do eiusmod tempor incididunt ut labore et dolore magna aliqua dolore magna sit</p>
</article>
<article class="service-card" style="left:141px;top:927px;padding-top:30px">
  <div class="icon" role="img" aria-label="Plant, sun and solar panel line icon"></div>
  <h3 style="margin-top:20px">Renewable Energy<br>Industries</h3>
  <p style="margin-top:18px">Lorem ipsum dolor sit amet, consectetur adipiscing elit, sed do eiusmod tempor incididunt ut labore et dolore magna aliqua dolore magna sit</p>
</article>
<article class="service-card" style="left:765px;top:927px;padding-top:40px">
  <div class="icon" role="img" aria-label="Gear with wrench line icon"></div>
  <h3 style="margin-top:22px">Utility</h3>
  <p style="margin-top:18px">Lorem ipsum dolor sit amet, consectetur adipiscing elit, sed do eiusmod tempor incididunt ut labore et dolore magna aliqua dolore magna sit</p>
</article>
<article class="service-card" style="left:453px;top:1081px;padding-top:38px">
  <div class="icon" role="img" aria-label="Pump jack line icon"></div>
  <h3 style="margin-top:24px">Construction</h3>
  <p style="margin-top:18px">Lorem ipsum dolor sit amet, consectetur adipiscing elit, sed do eiusmod tempor incididunt ut labore et dolore magna aliqua dolore magna sit</p>
</article>

<div class="abs" style="left:433px;top:1478px;width:130px;height:130px;background:var(--red)"></div>
<div class="about-panel"></div>
<div class="about-photo" role="img" aria-label="White aerial lift truck parked on a gravel yard in front of trees"></div>

<div class="brand abs" style="left:592px;top:1627px;font-size:40px">MARLOWBY</div>
<svg class="abs" style="left:596px;top:1697px" width="38" height="38" viewBox="0 0 38 38" fill="none" stroke="#e8202a" stroke-width="1.8">
  <path d="M2 19 Q19 4 36 19 Q19 34 2 19Z"/><circle cx="19" cy="19" r="6"/><circle cx="19" cy="19" r="2"/>
</svg>
<h3 class="about-heading" style="top:1697px">Our Vision</h3>
<p class="about-text" style="top:1748px">To be the leading provider of aerial access, geotechnical drilling, and service solutions, setting the standard for excellence in safety, efficiency, and environmental stewardship.</p>
<svg class="abs" style="left:596px;top:1846px" width="38" height="38" viewBox="0 0 38 38" fill="none" stroke="#e8202a" stroke-width="1.8">
  <circle cx="18" cy="20" r="16"/><circle cx="18" cy="20" r="10"/><circle cx="18" cy="20" r="4"/><path d="M18 20 L34 4 M28 4 H34 V10"/>
</svg>
<h3 class="about-heading" style="top:1846px">Our Mission</h3>
<p class="about-text" style="top:1900px">At Marlowby, our mission is to deliver unparalleled aerial access, geotechnical drilling, and service and maintenance solutions, consistently exceeding our clients' expectations. We strive to achieve this by investing in cutting-edge technology, fostering a culture of safety and continuous improvement, and prioritizing environmental sustainability. Through collaboration, integrity, and dedication, we aim to contribute to the success of our clients while maintaining the highest standards of quality and professionalism.</p>

<h2 class="section-title" style="top:2207px">OUR DIVISIONS</h2>

<div class="abs" style="left:311px;top:2297px;width:122px;height:120px;background:var(--red)"></div>
<a class="division" href="#" style="left:141px;background:linear-gradient(180deg,#3c5578 0%,#25406a 60%,#1e2e3f 100%)" role="img" aria-label="Aerial lift reaching up beside a wind turbine tower at dusk">
  <h3 style="top:177px">Aerial Access</h3>
  <p>Marlowby is a full-service wind energy service provider specializing in blade access &amp; repair , service and maintenance , &amp; trouble shooting on most wind turbine platforms.</p>
  <svg class="go" viewBox="0 0 20 20"><circle cx="10" cy="10" r="10" fill="#e8202a"/><path d="M5.5 10h8M10.5 6.5 14 10l-3.5 3.5" stroke="#fff" stroke-width="1.4" fill="none"/></svg>
</a>
<a class="division" href="#" style="left:459px;background:linear-gradient(180deg,#2c4233 0%,#3b5a3a 50%,#2a3526 100%)" role="img" aria-label="Red tracked geotechnical drill rig in a forest clearing">
  <h3 style="top:278px">Geotechnical Drilling</h3>
  <svg class="go" viewBox="0 0 20 20"><circle cx="10" cy="10" r="10" fill="#e8202a"/><path d="M5.5 10h8M10.5 6.5 14 10l-3.5 3.5" stroke="#fff" stroke-width="1.4" fill="none"/></svg>
</a>
<a class="division" href="#" style="left:778px;background:linear-gradient(160deg,#9fb6df 0%,#3b67b5 45%,#1d3f8c 100%)" role="img" aria-label="Wind turbine seen from below against a blue sky">
  <h3 style="top:268px">Renewable Energy<br>Services</h3>
  <svg class="go" viewBox="0 0 20 20"><circle cx="10" cy="10" r="10" fill="#e8202a"/><path d="M5.5 10h8M10.5 6.5 14 10l-3.5 3.5" stroke="#fff" stroke-width="1.4" fill="none"/></svg>
</a>

<p class="tagline"><span class="brand-word">MARLOWBY</span> Is A Full-service Wind Energy Service Provider<br>Specializing In Blade Access And Repair, Service And Maintenance,<br>And Trouble Shooting On Most Wind Turbine Platforms.</p>
<a class="btn" href="#" style="left:540px;top:2839px;width:116px;height:34px">Contact Us</a>

<footer class="site-footer">
  <div class="brand abs" style="left:0;width:1200px;text-align:center;top:78px;font-size:38px">MARLOWBY</div>
  <div class="rule" style="top:159px"></div>
  <nav class="footer-nav">
    <a style="left:322px" href="#">Home</a>
    <a style="left:414px" href="#">About</a>
    <a style="left:506px" href="#">Services</a>
    <a style="left:611px" href="#">Safety</a>
    <a style="left:704px" href="#">Careers</a>
    <a style="left:807px" href="#">Contact Us</a>
  </nav>
  <div class="rule" style="top:250px"></div>
  <div class="contact-item" style="left:199px">
    <svg width="30" height="30" viewBox="0 0 30 30" fill="none" stroke="#e8202a" stroke-width="1.4"><circle cx="15" cy="15" r="14"/><path d="M15 22s-5-5-5-9a5 5 0 0 1 10 0c0 4-5 9-5 9z"/><circle cx="15" cy="13" r="1.6"/></svg>
    <div>118 Ridgeline Road Harrow Flats<br>Alberta&nbsp; T0X 4B1</div>
  </div>
  <div class="contact-item" style="left:525px">
    <svg width="30" height="30" viewBox="0 0 30 30" fill="none" stroke="#e8202a" stroke-width="1.4"><circle cx="15" cy="15" r="14"/><path d="M10 9l3 0 1.5 3.5-2 1.3a8 8 0 0 0 3.7 3.7l1.3-2 3.5 1.5v3c-6 .5-11.5-5-11-11z"/></svg>
    <div><strong>Phone</strong><br>(555)-014-2290</div>
  </div>
  <div class="contact-item" style="left:791px">
    <svg width="30" height="30" viewBox="0 0 30 30" fill="none" stroke="#e8202a" stroke-width="1.4"><circle cx="15" cy="15" r="14"/><rect x="9" y="11" width="12" height="9" fill="#e8202a"/><path d="M9 11l6 5 6-5" stroke="#151515"/></svg>
    <div><strong>Email</strong><br>careers@marlowbyservices.example</div>
  </div>
  <div class="rule" style="top:355px"></div>
  <p class="copyright">© 2024 <strong>MARLOWBY</strong>. All Rights Reserved.</p>
</footer>

</body>
</html>
```